Parcelwise HQ letterhead and envelope

Design a formal (8.5x11) letterhead and envelope for sales outreach and legal matters. Using design input from https://www.parcelwisehq.example/ and the attached documents.

Industry/Entity Type

Software Service

Requirements
Must have
• These 4 hex colors are our official colors:
• #355c98 [blue]
• #1eb1a2 [teal]
• #fdba12 [gold]
• #f1653b [orange]
• So no other colors besides these should be used.

```html
<!DOCTYPE html>
<html lang="en">
<head>
<meta charset="utf-8">
<title>Parcelwise HQ Letterhead</title>
<link rel="stylesheet" href="https://fonts.googleapis.com/css2?family=Quicksand:wght@400;500&family=Arimo:wght@400&display=swap">
<style>
  :root {
    --brand-blue: #355c98;
    --brand-teal: #1eb1a2;
    --paper: #ffffff;
    --backdrop: #e9eaea;
    --watermark: #e6e9ee;
    --text: #4a4a4a;
  }
  html, body {
    margin: 0;
    width: 1200px;
    height: 936px;
    overflow: hidden;
    background: var(--backdrop);
  }
  .letterhead {
    position: absolute;
    left: 260px;
    top: 28px;
    width: 680px;
    height: 880px;
    background: var(--paper);
    box-shadow: 0 2px 10px rgba(0,0,0,0.08);
  }
  .brand {
    position: absolute;
    top: 52px;
    left: 50%;
    transform: translateX(-50%);
    display: flex;
    align-items: center;
    gap: 10px;
  }
  .brand-dot {
    width: 22px;
    height: 22px;
    border-radius: 50%;
    background: var(--brand-blue);
  }
  .brand-name {
    font-family: "Quicksand", sans-serif;
    font-weight: 500;
    font-size: 26px;
    color: var(--brand-blue);
    letter-spacing: 0.5px;
  }
  .watermark {
    position: absolute;
    left: 50%;
    top: 270px;
    width: 300px;
    height: 300px;
    margin-left: -150px;
  }
  .footer {
    position: absolute;
    left: 46px;
    right: 46px;
    bottom: 46px;
  }
  .contact {
    font-family: "Arimo", sans-serif;
    font-size: 11px;
    color: var(--text);
    line-height: 1.7;
  }
  .contact-row {
    display: flex;
    flex-wrap: wrap;
    gap: 14px;
  }
  .contact-item {
    display: inline-flex;
    align-items: center;
    gap: 5px;
  }
  .contact-icon {
    width: 11px;
    height: 11px;
  }
  .footer-rule {
    margin-top: 10px;
    height: 3px;
    background: var(--brand-teal);
  }
</style>
</head>
<body>
  <main class="letterhead">
    <header class="brand">
      <span class="brand-dot"></span>
      <span class="brand-name">Parcelwise HQ</span>
    </header>

    <svg class="watermark" viewBox="0 0 300 300" aria-hidden="true">
      <circle cx="150" cy="150" r="135" fill="none" stroke="var(--watermark)" stroke-width="14"/>
    </svg>

    <footer class="footer">
      <div class="contact">
        <div class="contact-row">
          <span class="contact-item">
            <svg class="contact-icon" viewBox="0 0 12 12"><circle cx="6" cy="6" r="6" fill="var(--brand-blue)"/><path d="M6 2.5a2 2 0 0 0-2 2c0 1.6 2 4.5 2 4.5s2-2.9 2-4.5a2 2 0 0 0-2-2z" fill="#fff"/></svg>
            214 Harbor Lane, Millbrook, MI 48012
          </span>
        </div>
        <div class="contact-row">
          <span class="contact-item">
            <svg class="contact-icon" viewBox="0 0 12 12"><circle cx="6" cy="6" r="6" fill="var(--brand-blue)"/><rect x="4" y="2.5" width="4" height="7" rx="0.8" fill="#fff"/></svg>
            (555) 210-4400
          </span>
          <span class="contact-item">
            <svg class="contact-icon" viewBox="0 0 12 12"><circle cx="6" cy="6" r="6" fill="var(--brand-blue)"/><path d="M3.5 3.2l1.4-.4.9 1.8-.9.7a4.5 4.5 0 0 0 1.8 1.8l.7-.9 1.8.9-.4 1.4C6 8.9 3.1 6 3.5 3.2z" fill="#fff"/></svg>
            (555) 300-7000(Main)
          </span>
          <span class="contact-item">
            <svg class="contact-icon" viewBox="0 0 12 12"><circle cx="6" cy="6" r="6" fill="var(--brand-blue)"/><rect x="2.8" y="3.8" width="6.4" height="4.4" fill="#fff"/><path d="M2.8 3.8L6 6.4l3.2-2.6" fill="none" stroke="var(--brand-blue)" stroke-width="0.7"/></svg>
            jdoe@parcelwisehq.example
          </span>
          <span class="contact-item">
            <svg class="contact-icon" viewBox="0 0 12 12"><circle cx="6" cy="6" r="6" fill="var(--brand-blue)"/><circle cx="6" cy="6" r="3.2" fill="none" stroke="#fff" stroke-width="0.8"/><path d="M2.8 6h6.4M6 2.8v6.4" stroke="#fff" stroke-width="0.7"/></svg>
            www.parcelwisehq.example
          </span>
        </div>
      </div>
      <div class="footer-rule"></div>
    </footer>
  </main>
</body>
</html>
```